Stationery Set for Velmora Company

I need to create full stationery design for my company; Business Cards, Envelops, Letter Heads, Calendar.
In the letter head and Envelops... only contact information and website links.
Our company is a Service Management company with different domains of innovative services including Technology Service Management, Education Services, Outsourcing Management, Events Management.
I need a modern and innovative design specially for the business card. I some transparent designs and I like it, but don't limit your innovation to what I mentioned. Sky is limit for your innovation.

Target Market(s)

Middle East & Africa

Industry/Entity Type

Business Management

Colors
34a7d8
0355a3
85acd3
86cae7
cee9f5
cfdeed
e4daeb
f3f1f8
ecf7fb

Requirements
Must have
• Name, Title, Email, Mobile
Nice to have
• We have multiple locations in USA, KSA, EGY, so I need ideas about how to include all contact details maybe QR / Barcode or something else.
• Please see our locations and contact information: www.brightvelmora.example
Should not have
• Too much text

```html
<!DOCTYPE html>
<html lang="en">
<head>
<meta charset="utf-8">
<title>Velmora Company — Business Card</title>
<link rel="stylesheet" href="https://fonts.googleapis.com/css2?family=Open+Sans:wght@400;600;700&display=swap">
<style>
  :root {
    --bg: #e9ecef;
    --card: #ffffff;
    --card-edge: #d9dde2;
    --panel-top: #4677bf;
    --panel-bottom: #2e5a9e;
    --panel-rule: rgba(255,255,255,0.45);
    --brand: #0355a3;
    --brand-soft: #85acd3;
    --ink: #1a1a1a;
    --on-panel: #ffffff;
  }
  * { box-sizing: border-box; margin: 0; padding: 0; }
  html, body { width: 1200px; height: 843px; overflow: hidden; }
  body {
    background: var(--bg);
    font-family: "Open Sans", Arial, sans-serif;
    display: flex;
    align-items: center;
    justify-content: center;
    gap: 60px;
  }
  .card {
    width: 525px;
    height: 300px;
    background: var(--card);
    border: 1px solid var(--card-edge);
    box-shadow: 0 6px 18px rgba(0,0,0,0.12);
    position: relative;
    overflow: hidden;
  }
  .card--logo {
    display: flex;
    align-items: center;
    justify-content: center;
  }
  .brand-name {
    font-weight: 700;
    color: var(--brand);
    font-size: 46px;
    letter-spacing: 1px;
    display: flex;
    align-items: center;
    gap: 10px;
  }
  .brand-name .brand-dot {
    width: 14px; height: 14px; border-radius: 50%;
    background: var(--brand-soft);
  }
  .card--contact { display: flex; }
  .contact-panel {
    width: 248px;
    height: 100%;
    background: linear-gradient(160deg, var(--panel-top), var(--panel-bottom));
    color: var(--on-panel);
    padding: 20px 16px 18px 18px;
    font-size: 11.5px;
    line-height: 1.35;
  }
  .contact-lines { list-style: none; }
  .contact-lines li { display: flex; align-items: center; gap: 8px; }
  .contact-lines svg { width: 11px; height: 11px; flex: none; }
  .contact-lines .no-icon { padding-left: 19px; }
  .rule { border: 0; border-top: 1px solid var(--panel-rule); margin: 10px 0 9px; }
  .office-title { font-weight: 700; text-transform: uppercase; }
  .identity {
    flex: 1;
    position: relative;
    padding: 0 26px;
  }
  .identity .brand-name {
    position: absolute;
    top: 70px; left: 0; right: 0;
    justify-content: center;
    font-size: 34px;
  }
  .identity .brand-name .brand-dot { width: 10px; height: 10px; }
  .person { position: absolute; left: 26px; bottom: 52px; }
  .person-name { color: var(--brand); font-weight: 600; font-size: 18px; }
  .person-title { color: var(--ink); font-size: 13px; }
</style>
</head>
<body>
  <section class="card card--logo" aria-label="Business card front">
    <div class="brand-name"><span class="brand-dot"></span>Velmora</div>
  </section>

  <section class="card card--contact" aria-label="Business card back">
    <div class="contact-panel">
      <ul class="contact-lines">
        <li><svg viewBox="0 0 12 12"><path d="M3 1 L5 3 L4 4.5 Q5.5 7 7.5 8 L9 7 L11 9 L9.5 11 Q4 10 1 3 Z" fill="#fff"/></svg>+1.555 010 2040 (USA)</li>
        <li><svg viewBox="0 0 12 12"><rect x="3" y="0.5" width="6" height="11" rx="1" fill="none" stroke="#fff"/><circle cx="6" cy="9.5" r="0.7" fill="#fff"/></svg>+966 5 0000 1122 (Saudi)</li>
        <li class="no-icon">+1.555 010 2040</li>
        <li><svg viewBox="0 0 12 12"><rect x="0.5" y="2.5" width="11" height="7" fill="#fff"/><path d="M0.5 2.5 L6 7 L11.5 2.5" fill="none" stroke="#2e5a9e"/></svg>info@brightvelmora.example</li>
      </ul>
      <hr class="rule">
      <p class="office-title">USA</p>
      <p>120 Harbor Point Lane<br>4th Floor Lakeview City<br>CA 90000 US</p>
      <hr class="rule">
      <p class="office-title">Saudi Arabia</p>
      <p>Riyadh, Al Noor District,<br>Palm Garden St.<br>Cedar Buildings<br>Block 4C 1st Floor A12, A14</p>
    </div>
    <div class="identity">
      <div class="brand-name"><span class="brand-dot"></span>Velmora</div>
      <div class="person">
        <p class="person-name">Daniel Reyes</p>
        <p class="person-title">CEO/Founder</p>
      </div>
    </div>
  </section>
</body>
</html>
```